Wealth Education Business Needs Sharp Business Card Design

We need a business card design for a recently launched investor education business called Harbor Crest.

The final design should promote security, empowerment, self improvement and financial gain. The card will ideally promote the stature of the business.

For more information and colours please visit harborcrest.com.au

Target Market(s)

Corporate executives and high net worth individuals

Industry/Entity Type

Education

Contact Information for Business Card

```html
<!DOCTYPE html>
<html lang="en">
<head>
<meta charset="utf-8">
<title>Harbor Crest – Business Card</title>
<link href="https://fonts.googleapis.com/css2?family=Open+Sans:wght@400;600;700&family=Oswald:wght@500;600&display=swap" rel="stylesheet">
<style>
  :root {
    --navy: #1b2a3d;
    --white: #ffffff;
    --paper: #e9eaec;
    --teal: #1b8b8c;
    --grey-logo: #a3a7ac;
    --ink: #2b2b2b;
    --muted: #5d6670;
    --rule: #c9ccd0;
  }
  * { margin: 0; padding: 0; box-sizing: border-box; }
  html, body { width: 1200px; height: 902px; overflow: hidden; }
  body {
    background: var(--paper);
    font-family: "Open Sans", Arial, sans-serif;
    display: flex;
    align-items: center;
    justify-content: center;
    gap: 40px;
  }
  .card {
    width: 540px;
    height: 309px;
    border-radius: 16px;
    overflow: hidden;
    box-shadow: 0 6px 18px rgba(0,0,0,0.18);
    position: relative;
  }

  /* Front */
  .card-front {
    background: var(--navy);
    display: flex;
    flex-direction: column;
    align-items: center;
    justify-content: center;
    color: var(--white);
  }
  .brand-row {
    display: flex;
    align-items: center;
    gap: 18px;
  }
  .brand-dot {
    width: 26px; height: 26px;
    border-radius: 50%;
    background: var(--teal);
    flex: none;
  }
  .brand-text { display: flex; flex-direction: column; }
  .brand-name {
    font-family: "Oswald", "Arial Narrow", sans-serif;
    font-weight: 600;
    font-size: 38px;
    line-height: 1.1;
    letter-spacing: 3px;
    text-transform: uppercase;
    color: var(--white);
  }
  .tagline {
    font-family: "Oswald", "Arial Narrow", sans-serif;
    font-size: 15px;
    font-weight: 500;
    letter-spacing: 4.2px;
    color: var(--teal);
    text-transform: uppercase;
  }
  .front-url {
    margin-top: 44px;
    font-size: 13px;
    color: var(--grey-logo);
    letter-spacing: 0.5px;
  }

  /* Back */
  .card-back { background: var(--white); }
  .back-band {
    height: 44%;
    background: var(--navy);
    display: flex;
    align-items: center;
    justify-content: center;
    gap: 16px;
  }
  .back-band .brand-name { color: var(--grey-logo); font-size: 36px; letter-spacing: 5px; }
  .back-band .brand-dot { width: 22px; height: 22px; }
  .back-body {
    height: 56%;
    display: flex;
    align-items: center;
    padding: 0 28px;
  }
  .person { flex: 1; text-align: right; padding-right: 22px; }
  .person-name { font-size: 21px; font-weight: 700; color: var(--ink); text-transform: uppercase; line-height: 1.2; }
  .person-name .first { color: var(--teal); }
  .person-title { font-size: 12px; color: var(--ink); margin-bottom: 14px; }
  .address { font-size: 13px; color: var(--ink); line-height: 1.45; }
  .divider { width: 1px; align-self: stretch; margin: 26px 0; background: var(--rule); }
  .contacts { flex: 1; list-style: none; padding-left: 22px; }
  .contacts li {
    display: flex; align-items: center; gap: 10px;
    font-size: 12.5px; color: var(--muted); line-height: 1.9;
    white-space: nowrap;
  }
  .contacts svg { width: 12px; height: 12px; fill: var(--ink); flex: none; }
</style>
</head>
<body>
  <section class="card card-front">
    <div class="brand-row">
      <span class="brand-dot"></span>
      <div class="brand-text">
        <span class="brand-name">Harbor Crest</span>
        <span class="tagline">Plan Build Flourish</span>
      </div>
    </div>
    <div class="front-url">www.harborcrest.com.au</div>
  </section>

  <section class="card card-back">
    <div class="back-band">
      <span class="brand-dot"></span>
      <span class="brand-name">Harbor Crest</span>
    </div>
    <div class="back-body">
      <div class="person">
        <div class="person-name"><span class="first">Your</span> Name</div>
        <div class="person-title">Title</div>
        <div class="address">Level 4, 72 Garden Row<br>Melbourne VIC 3000</div>
      </div>
      <div class="divider"></div>
      <ul class="contacts">
        <li>
          <svg viewBox="0 0 24 24" aria-hidden="true"><path d="M6.6 10.8a15.1 15.1 0 0 0 6.6 6.6l2.2-2.2a1 1 0 0 1 1-.25 11.4 11.4 0 0 0 3.6.57 1 1 0 0 1 1 1V20a1 1 0 0 1-1 1A17 17 0 0 1 3 4a1 1 0 0 1 1-1h3.5a1 1 0 0 1 1 1c0 1.25.2 2.450.57 3.57a1 1 0 0 1-.25 1z"/></svg>
          1300 555 210
        </li>
        <li>
          <svg viewBox="0 0 24 24" aria-hidden="true"><path d="M3 3h8v18H3zM13 7h8v14h-8zM15 10h4v2h-4zM15 14h4v2h-4z"/></svg>
          +613 9000 4120
        </li>
        <li>
          <svg viewBox="0 0 24 24" aria-hidden="true"><path d="M2 5h20v14H2zM4 7v.5l8 5 8-5V7z" fill-rule="evenodd"/></svg>
          support@harborcrest.com.au
        </li>
        <li>
          <svg viewBox="0 0 24 24" aria-hidden="true"><path d="M12 2a10 10 0 1 0 0 20 10 10 0 0 0 0-20zm0 2c.9 1.2 1.6 2.6 2 4h-4c.4-1.4 1.1-2.8 2-4zM4.3 14a8 8 0 0 1 0-4h3.4a16 16 0 0 0 0 4zm5.7 0a14 14 0 0 1 0-4h4a14 14 0 0 1 0 4zm6.3 0a16 16 0 0 0 0-4h3.4a8 8 0 0 1 0 4zM12 20c-.9-1.2-1.6-2.6-2-4h4c-.4 1.4-1.1 2.8-2 4z"/></svg>
          www.harborcrest.com.au
        </li>
      </ul>
    </div>
  </section>
</body>
</html>
```